Velura Nocturna

Website for a night club with live music and cabaret dancers. I would like to have the following Menu: 1.) Home; 2) The Facilities; 3) The Show; 4) Other Attractions; 5) Videos & Fotos; 6) Program; 7) Reservations; 8) Membership; 9) Contacts.

The pages should be easily editable and allow to enter text, including the menu since the final version will be in both English and Portuguese. It should have a toggle or links for the Portuguese language and the English Language.

The night club itself is called "VELURA NOCTURNA"; and its URL is www.veluranocturna.example.

```html
<!DOCTYPE html>
<html lang="en">
<head>
<meta charset="utf-8">
<title>Velura Nocturna</title>
<link rel="stylesheet" href="https://fonts.googleapis.com/css2?family=Patua+One&family=Alfa+Slab+One&family=PT+Sans:wght@400;700&family=Source+Sans+3:wght@300;400&display=swap">
<style>
:root{
  --bg:#0b0907;
  --gold:#c9a227;
  --gold-dark:#3a2a08;
  --orange:#ff9f12;
  --orange-light:#ffb324;
  --orange-active:#e07a0a;
  --nav-text:#2b1a05;
  --white:#ffffff;
  --muted:#8a8580;
  --link:#f2c21b;
  --hero:#1d1b1a;
  --icon:#9a9a9a;
}
*{margin:0;padding:0;box-sizing:border-box}
html,body{width:1200px;height:1200px;overflow:hidden}
body{
  position:relative;
  background:
    radial-gradient(ellipse 900px 500px at 600px 330px, rgba(120,86,15,.55), transparent 70%),
    linear-gradient(180deg,#1a1408 0%,#2a1f08 45%,#0c0a07 70%,#070707 100%);
  color:var(--white);
  font-family:"Source Sans 3",sans-serif;
}
.brand{position:absolute;left:124px;top:30px;font-family:"Patua One",serif;font-size:38px;color:var(--gold);letter-spacing:1px}
.social{position:absolute;left:874px;top:40px;display:flex;gap:8px;list-style:none}
.social li{width:32px;height:32px;border-radius:50%;background:#e6e6e6;box-shadow:0 0 0 2px #bdbdbd inset;display:flex;align-items:center;justify-content:center}
.lang{position:absolute;right:134px;top:84px;display:flex;gap:6px;font-family:"PT Sans",sans-serif;font-size:12px;color:var(--muted)}
.lang a{color:var(--muted);text-decoration:none}
.lang a.current{color:var(--orange)}
.nav{position:absolute;left:100px;top:110px;width:1000px;height:54px;background:linear-gradient(180deg,var(--orange-light),var(--orange));display:flex;align-items:center;justify-content:space-between;padding:0 47px 0 29px}
.nav a,.footer-nav a{font-family:"Patua One",serif;font-size:15px;color:var(--nav-text);text-decoration:none;white-space:nowrap}
.nav a.active{background:var(--orange-active);color:var(--white);height:54px;line-height:54px;padding:0 14px}
.hero{position:absolute;left:100px;top:164px;width:1000px;height:436px;background:var(--hero);overflow:hidden}
.hero-photo{position:absolute;right:0;top:0;width:620px;height:436px;background:radial-gradient(ellipse at 55% 30%,#d8326f 0%,#a0287a 30%,#3a1a2a 65%,var(--hero) 100%)}
.hero h1{position:absolute;left:64px;top:110px;font-family:"Alfa Slab One",serif;font-weight:400;font-size:34px;word-spacing:8px}
.hero p{position:absolute;left:64px;top:164px;width:272px;font-size:14px;font-weight:300;line-height:18px;text-align:justify}
.dots{position:absolute;left:70px;top:312px;display:flex;gap:10px}
.dots span{width:12px;height:12px;border-radius:50%;background:var(--white)}
.dots span.on{background:var(--orange)}
.hero-mark{position:absolute;left:64px;top:354px;font-family:"Patua One",serif;font-size:36px;color:var(--gold-dark)}
.intro h2{position:absolute;left:124px;top:616px;font-family:"PT Sans",sans-serif;font-size:31px;font-weight:700}
.intro p{position:absolute;left:130px;top:662px;font-size:19px;font-weight:300}
.col{position:absolute;top:700px;width:302px}
.col h3{font-weight:300;font-size:23px;margin:0 0 10px 4px;height:30px}
.col .img{width:302px;height:162px}
.col .text{font-family:"PT Sans",sans-serif;font-size:13.5px;line-height:18px;padding:0 6px;margin-top:16px;text-align:justify}
.col .more{display:block;margin:22px 0 0 6px;color:var(--link);font-family:"PT Sans",sans-serif;font-size:13.5px;text-decoration:none}
.c1{left:130px}.c2{left:449px}.c3{left:767px}
.c1 .img{height:326px;position:relative;background:radial-gradient(circle at 50% 40%,#7a3a90,#2a3a30 50%,#141414)}
.c2 .img{background:linear-gradient(90deg,#c8b23a,#d8463a 40%,#6aa24a 70%,#c8b23a)}
.c3 .img{background:linear-gradient(180deg,#7e8e9e 0%,#4a5560 45%,#2a3a20 75%,#1a1a1a)}
.play{position:absolute;left:131px;top:140px}
.footer-nav{position:absolute;left:100px;top:1102px;width:1000px;display:flex;justify-content:space-between;padding:0 47px 0 43px}
.footer-nav a{color:var(--muted)}
.copy{position:absolute;left:0;width:1150px;text-align:center;top:1144px;font-size:12px;color:#4a4744}
</style>
</head>
<body>
<header>
  <div class="brand">Velura Nocturna</div>
  <ul class="social" aria-label="Social links">
    <li><svg width="16" height="16" viewBox="0 0 16 16"><path d="M6.5 9.5l3-3M7 4.5l1.5-1.5a2.5 2.5 0 013.5 3.5L10.5 8M9 11.5L7.5 13a2.5 2.5 0 01-3.5-3.5L5.5 8" fill="none" stroke="var(--icon)" stroke-width="1.6" stroke-linecap="round"/></svg></li>
    <li><svg width="16" height="16" viewBox="0 0 16 16"><path d="M6.5 9.5l3-3M7 4.5l1.5-1.5a2.5 2.5 0 013.5 3.5L10.5 8M9 11.5L7.5 13a2.5 2.5 0 01-3.5-3.5L5.5 8" fill="none" stroke="var(--icon)" stroke-width="1.6" stroke-linecap="round"/></svg></li>
    <li><svg width="16" height="16" viewBox="0 0 16 16"><path d="M6.5 9.5l3-3M7 4.5l1.5-1.5a2.5 2.5 0 013.5 3.5L10.5 8M9 11.5L7.5 13a2.5 2.5 0 01-3.5-3.5L5.5 8" fill="none" stroke="var(--icon)" stroke-width="1.6" stroke-linecap="round"/></svg></li>
    <li><svg width="16" height="16" viewBox="0 0 16 16"><path d="M6.5 9.5l3-3M7 4.5l1.5-1.5a2.5 2.5 0 013.5 3.5L10.5 8M9 11.5L7.5 13a2.5 2.5 0 01-3.5-3.5L5.5 8" fill="none" stroke="var(--icon)" stroke-width="1.6" stroke-linecap="round"/></svg></li>
    <li><svg width="16" height="16" viewBox="0 0 16 16"><path d="M6.5 9.5l3-3M7 4.5l1.5-1.5a2.5 2.5 0 013.5 3.5L10.5 8M9 11.5L7.5 13a2.5 2.5 0 01-3.5-3.5L5.5 8" fill="none" stroke="var(--icon)" stroke-width="1.6" stroke-linecap="round"/></svg></li>
  </ul>
  <div class="lang" aria-label="Language"><a class="current" href="#" lang="en">EN</a><span>|</span><a href="#" lang="pt">PT</a></div>
  <nav class="nav">
    <a class="active" href="#">Home</a><a href="#">The Facilities</a><a href="#">The Show</a><a href="#">Other Attractions</a><a href="#">Videos &amp; Fotos</a><a href="#">Program</a><a href="#">Reservations</a><a href="#">Membership</a><a href="#">Contacts</a>
  </nav>
</header>
<section class="hero">
  <div class="hero-photo" role="img" aria-label="Three cabaret dancers in colourful feather headdresses"></div>
  <h1>Lorium Ipsum</h1>
  <p>Duis aute irure dolor in reprehenderit in voluptate velit esse cillum dolore eu fugiat nulla pariatur. Excepteur sint occaecat cupi-datat non proident,</p>
  <div class="dots"><span></span><span></span><span class="on"></span></div>
  <div class="hero-mark">Velura Nocturna</div>
</section>
<section class="intro">
  <h2>We Have the Diverse Range of Music</h2>
  <p>We Have Everything to Make Your Night Bright!</p>
</section>
<article class="col c1">
  <h3>Videos &amp; Fotos</h3>
  <div class="img" role="img" aria-label="Video still of dancers in feathered costumes on stage">
    <svg class="play" width="40" height="46" viewBox="0 0 40 46"><circle cx="20" cy="23" r="20" fill="rgba(255,255,255,.35)"/><path d="M14 11 L32 23 L14 35 Z" fill="#1a1a1a"/></svg>
  </div>
</article>
<article class="col c2">
  <h3>The Show</h3>
  <div class="img" role="img" aria-label="Line of dancers in bright floral costumes"></div>
  <p class="text">Perspiciatis unde omnis iste natus error sit volup-tatem accusantium doloremque laudantium, totam rem aperiam, eaque ipsa quae ab illo inven-tore veritatis et quasi architecto...</p>
  <a class="more" href="#">Read more ...</a>
</article>
<article class="col c3">
  <h3>Contact Us</h3>
  <div class="img" role="img" aria-label="Club building exterior with palm trees"></div>
  <p class="text">Perspiciatis unde omnis iste natus error sit volup-tatem accusantium doloremque laudantium, totam rem aperiam, eaque ipsa quae ab illo inven-tore veritatis et quasi architecto...</p>
  <a class="more" href="#">Read more ...</a>
</article>
<footer>
  <nav class="footer-nav">
    <a href="#">Home</a><a href="#">The Facilities</a><a href="#">The Show</a><a href="#">Other Attractions</a><a href="#">Videos &amp; Fotos</a><a href="#">Program</a><a href="#">Reservations</a><a href="#">Membership</a><a href="#">Contacts</a>
  </nav>
  <p class="copy">© 2014.www.veluranocturna.example</p>
</footer>
</body>
</html>
```